WordPress Site That Reviews Footwear

We need a wordpress web design for an affiliate site called PaceKite. We review and do roundups on footwear products. The final design should be clean and mobile friendly. The site should be built with Gutenberg page builder. We like the design of https://lunavessel.com/.
Updates

Need extra days to review

Target Market(s)

USA

Industry/Entity Type

Footwear

Logo Text

PaceKite

Number of Pages Required

4 page

Font styles to use
Serif
Sans Serif

Requirements
Must have
• Wordpress site
Blog post
Page
Categories
Homepage

```html
<!DOCTYPE html>
<html lang="en">
<head>
<meta charset="utf-8">
<title>PaceKite — Footwear Reviews</title>
<link href="https://fonts.googleapis.com/css2?family=Libre+Baskerville:wght@400;700&family=Lato:wght@400;700&family=Tinos:wght@400;700&display=swap" rel="stylesheet">
<style>
:root{
  --ink:#1d1d2b;
  --muted:#333;
  --white:#fff;
  --bg-soft:#eef0f4;
  --bg-featured:#e8ecf0;
  --bg-footer:#e4e8ec;
  --slate:#4d7186;
  --slate-dark:#46697d;
  --accent:#e7a51a;
  --line:#d4d8dd;
}
*{box-sizing:border-box;margin:0;padding:0}
html,body{width:1200px;height:2430px;overflow:hidden}
body{position:relative;background:var(--bg-soft);color:var(--ink);font-family:"Tinos",serif}
.abs{position:absolute}
.serif-head{font-family:"Libre Baskerville",serif}
.sans{font-family:"Lato",sans-serif}

/* header */
.site-header{left:0;top:0;width:1200px;height:75px;background:var(--white)}
.nav-link{top:32px;font-size:12px;letter-spacing:.2px;color:var(--ink);font-family:"Tinos",serif}
.nav-link .caret{font-size:9px;margin-left:3px}
.brand-top{left:0;width:1200px;top:14px;text-align:center;font-family:"Libre Baskerville",serif;font-size:32px;letter-spacing:1px}
.social-sq{top:30px;width:16px;height:16px;border-radius:3px;background:var(--ink)}

/* hero */
.hero{left:0;top:75px;width:1200px;height:482px;background:linear-gradient(90deg,#e6e7ea 0%,#dcdde1 35%,#8d8f94 55%,#9a9ca1 68%,#e4e5e8 85%,#ebecef 100%)}
.hero-title{left:106px;top:180px;font-family:"Libre Baskerville",serif;font-size:72px;letter-spacing:-1px;color:var(--ink)}
.hero-text{left:112px;top:272px;width:370px;font-family:"Lato",sans-serif;font-size:13px;line-height:26px;color:var(--muted)}
.hero-cta{left:111px;top:345px;font-size:13px;letter-spacing:2.2px;color:var(--ink)}
.hero-cta .arrow{color:var(--accent);margin-left:8px}
.cat-card{width:172px;height:130px;background:var(--white);border-radius:6px;text-align:center}
.cat-card .icon{width:50px;height:34px;margin:22px auto 0;border-radius:4px;background:#d9dbe0}
.cat-card .label{margin-top:14px;font-size:21px;color:var(--ink)}

/* welcome */
.welcome{left:0;top:557px;width:1200px;height:294px;background:var(--bg-soft);overflow:hidden}
.welcome h2{left:0;width:1200px;top:70px;text-align:center;font-family:"Libre Baskerville",serif;font-size:34px;font-weight:400}
.welcome p{left:240px;width:720px;top:126px;text-align:center;font-family:"Lato",sans-serif;font-size:13.5px;line-height:27px;color:var(--muted)}

/* features */
.features-panel{left:0;top:851px;width:726px;height:607px;background:linear-gradient(160deg,#4a6f86 0%,#4f7184 50%,#587a88 100%)}
.features-photo{left:726px;top:851px;width:474px;height:607px;background:linear-gradient(135deg,#8b8b8b,#6f6f70 60%,#4a4a4b)}
.feature h3{font-family:"Libre Baskerville",serif;font-size:28px;font-weight:400;color:var(--white)}
.feature p{margin-top:10px;width:270px;font-size:15px;line-height:23px;color:#eef2f5}
.btn-pill{display:inline-block;margin-top:28px;width:150px;height:49px;line-height:49px;border-radius:25px;background:var(--white);text-align:center;font-size:14px;color:var(--ink)}

/* featured products */
.featured{left:0;top:1458px;width:1200px;height:662px;background:var(--bg-featured)}
.featured h2{left:0;width:1200px;top:65px;text-align:center;font-family:"Libre Baskerville",serif;font-size:34px;font-weight:400}
.featured .intro{left:220px;width:760px;top:115px;text-align:center;font-size:15.5px;line-height:28px;color:var(--muted)}
.product{width:307px}
.product .thumb{height:188px;border-radius:6px}
.product .meta{margin-top:18px;font-family:"Libre Baskerville",serif;font-size:11px;color:var(--slate);letter-spacing:.3px}
.product .meta .dot{display:inline-block;width:8px;height:8px;background:var(--slate);margin:0 6px;vertical-align:0}
.product h4{margin-top:10px;font-family:"Libre Baskerville",serif;font-size:19px;font-weight:400;line-height:27px}
.product .more{margin-top:20px;font-size:13px;letter-spacing:.3px}
.chev{top:1785px;width:26px;height:40px}

/* footer */
.site-footer{left:0;top:2120px;width:1200px;height:310px;background:var(--bg-footer)}
.foot-brand{left:110px;top:60px;font-family:"Libre Baskerville",serif;font-size:38px}
.foot-about{left:112px;top:124px;width:240px;font-size:10.5px;line-height:21px;color:var(--muted)}
.foot-title{top:65px;font-family:"Libre Baskerville",serif;font-size:16px}
.foot-text{font-size:11.5px;line-height:20px;color:var(--muted)}
.foot-links a{display:block;font-size:11.5px;color:var(--muted);text-decoration:none;margin-bottom:10px}
.newsletter-input{left:772px;top:103px;width:204px;height:47px;background:var(--white);border:1px solid var(--line);font-size:11px;color:#888;padding:15px 19px}
.newsletter-btn{left:976px;top:103px;width:112px;height:47px;background:var(--slate);color:var(--white);font-family:"Libre Baskerville",serif;font-size:15px;letter-spacing:.8px;text-align:center;line-height:47px}
.social-ring{top:178px;width:38px;height:38px;border-radius:50%;border:1px solid var(--line);background:var(--white)}
.foot-rule{left:110px;top:247px;width:980px;height:1px;background:var(--line)}
.copyright{left:0;width:1200px;top:272px;text-align:center;font-size:11.5px;color:var(--muted)}
</style>
</head>
<body>

<header class="abs site-header">
  <span class="abs nav-link" style="left:112px">PRODUCTS<span class="caret">&#8964;</span></span>
  <span class="abs nav-link" style="left:209px">FOOTWEAR<span class="caret">&#8964;</span></span>
  <span class="abs nav-link" style="left:317px">CONCERNS<span class="caret">&#8964;</span></span>
  <span class="abs nav-link" style="left:419px">REVIEWS<span class="caret">&#8964;</span></span>
  <div class="abs brand-top">PaceKite</div>
  <span class="abs nav-link" style="left:828px">ABOUT</span>
  <span class="abs nav-link" style="left:893px">CONTACT</span>
  <span class="abs social-sq" style="left:1002px"></span>
  <span class="abs social-sq" style="left:1037px"></span>
  <span class="abs social-sq" style="left:1071px"></span>
</header>

<section class="abs hero" role="img" aria-label="Soft grey photo of a person walking in trousers and sneakers">
</section>
<div class="abs hero-title">PaceKite</div>
<p class="abs hero-text">Temporibus autem quibusdam et aut officiis debitis aut rerum eveniet ut et voluptates repudiandae sint et molestiae</p>
<div class="abs hero-cta">CHECK OUT A FEW OF OUR FAVORITES<span class="arrow">&#10230;</span></div>

<div class="abs cat-card" style="left:539px;top:170px"><div class="icon" role="img" aria-label="Sneaker icon"></div><div class="label">Esse Cillum</div></div>
<div class="abs cat-card" style="left:727px;top:170px"><div class="icon" role="img" aria-label="Pump shoe icon"></div><div class="label">Necessitatibus</div></div>
<div class="abs cat-card" style="left:916px;top:170px"><div class="icon" role="img" aria-label="Loafers icon"></div><div class="label">Cumque Nihi</div></div>
<div class="abs cat-card" style="left:539px;top:333px"><div class="icon" role="img" aria-label="Ankle boot icon"></div><div class="label">Dicta Sunt</div></div>
<div class="abs cat-card" style="left:727px;top:333px"><div class="icon" role="img" aria-label="Strappy heel icon"></div><div class="label">Exercitation</div></div>
<div class="abs cat-card" style="left:916px;top:333px"><div class="icon" role="img" aria-label="High heel icon"></div><div class="label">Dolorem Ipsum</div></div>

<section class="abs welcome">
  <svg class="abs" style="left:0;top:0" width="1200" height="294" viewBox="0 0 1200 294">
    <path d="M500 294 C600 120 700 10 820 8 C940 6 1060 160 1165 294 Z" fill="#f8f9fa"/>
    <path d="M15 294 C50 250 100 235 140 236 C190 238 230 260 250 294 Z" fill="#f8f9fa"/>
    <circle cx="347" cy="155" r="50" fill="#f8f9fa"/>
  </svg>
  <h2 class="abs">Welcome to PaceKite</h2>
  <p class="abs">Temporibus autem quibusdam et aut officiis debitis aut rerum necessitatibus saepe eveniet ut et voluptates repudiandae sint et molestiae non recusandae.</p>
</section>

<section class="abs features-panel" role="img" aria-label="Blue-tinted photo of a runner's legs on a path"></section>
<div class="abs features-photo" role="img" aria-label="Black leather shoes with shoe brushes on grey stone"></div>

<div class="abs feature" style="left:111px;top:935px">
  <h3>Consectetur</h3>
  <p>Lorem ipsum dolor sit amet, consectetur adipiscing elit, sed do eiusmod tempor incididunt ut labore et dolore magna.</p>
  <span class="btn-pill">LEARN MORE</span>
</div>
<div class="abs feature" style="left:420px;top:935px">
  <h3>Dolorem Ipsum</h3>
  <p>Lorem ipsum dolor sit amet, consectetur adipiscing elit, sed do eiusmod tempor incididunt ut labore et dolore magna.</p>
  <span class="btn-pill">LEARN MORE</span>
</div>
<div class="abs feature" style="left:111px;top:1166px">
  <h3>Magni Dolores</h3>
  <p>Lorem ipsum dolor sit amet, consectetur adipiscing elit, sed do eiusmod tempor incididunt ut labore et dolore magna.</p>
  <span class="btn-pill">LEARN MORE</span>
</div>
<div class="abs feature" style="left:420px;top:1166px">
  <h3>Exercitationem</h3>
  <p>Lorem ipsum dolor sit amet, consectetur adipiscing elit, sed do eiusmod tempor incididunt ut labore et dolore magna.</p>
  <span class="btn-pill">LEARN MORE</span>
</div>

<section class="abs featured">
  <h2 class="abs">Featured Products</h2>
  <p class="abs intro">Sed ut perspiciatis unde omnis iste natus error sit voluptatem accusantium doloremque laudantium, totam rem aperiam, eaque ipsa quae ab illo inventore veritatis et quasi architecto beatae vitae dicta sunt explicabo.</p>
</section>

<svg class="abs chev" style="left:60px" viewBox="0 0 26 40"><path d="M22 3 L6 20 L22 37" fill="none" stroke="#c9d0d7" stroke-width="6"/></svg>
<svg class="abs chev" style="left:1113px" viewBox="0 0 26 40"><path d="M4 3 L20 20 L4 37" fill="none" stroke="#c9d0d7" stroke-width="6"/></svg>

<article class="abs product" style="left:111px;top:1691px">
  <div class="thumb" role="img" aria-label="Pair of red baby sneakers on white flowers" style="background:linear-gradient(135deg,#e6e6e6,#d8c3c6 50%,#e9e9e9)"></div>
  <div class="meta">PRODUCT REVIEWS<span class="dot"></span>2 MONTHS AGO</div>
  <h4>Excepteur sint occaecat cupidatat non proident</h4>
  <div class="more">READ MORE &#10230;</div>
</article>
<article class="abs product" style="left:446px;top:1691px">
  <div class="thumb" role="img" aria-label="Row of small colourful children's shoes on pale wood" style="background:linear-gradient(135deg,#efede6,#d9d8cf 50%,#eeece4)"></div>
  <div class="meta">PRODUCT REVIEWS<span class="dot"></span>6 MONTHS AGO</div>
  <h4>Temporibus autem quibusdam et aut officiis debitis</h4>
  <div class="more">READ MORE &#10230;</div>
</article>
<article class="abs product" style="left:781px;top:1691px">
  <div class="thumb" role="img" aria-label="White baby shoes against a light blue wall" style="background:linear-gradient(180deg,#a5d8f1 0%,#9fd2ed 70%,#c9d6de 100%)"></div>
  <div class="meta">PRODUCT REVIEWS<span class="dot"></span>5 MONTHS AGO</div>
  <h4>Et harum quidem rerum facilis est et expedita distinctio</h4>
  <div class="more">READ MORE &#10230;</div>
</article>

<footer class="abs site-footer">
  <div class="abs foot-brand">PaceKite</div>
  <p class="abs foot-about">At vero eos et accusamus et iusto odio dignissimos ducimus qui blanditiis praesentium voluptatum deleniti atque corrupti quos dolores</p>

  <div class="abs foot-title" style="left:396px">Where to Find us</div>
  <svg class="abs" style="left:395px;top:110px" width="10" height="14" viewBox="0 0 10 14"><path d="M5 0 C2 0 0 2 0 5 C0 8 5 14 5 14 C5 14 10 8 10 5 C10 2 8 0 5 0 Z M5 3 A2 2 0 1 1 5 7 A2 2 0 1 1 5 3 Z" fill="#1d1d2b"/></svg>
  <p class="abs foot-text" style="left:411px;top:107px">1003 Street Name,<br>City Name, Country<br>V8W 1V7</p>
  <svg class="abs" style="left:395px;top:201px" width="12" height="12" viewBox="0 0 12 12"><path d="M2.5 0 L4.5 3 L3.3 4.5 C4 6 6 8 7.5 8.7 L9 7.5 L12 9.5 L10.5 12 C5 11.5 0.5 7 0 1.5 Z" fill="#1d1d2b"/></svg>
  <p class="abs foot-text" style="left:411px;top:197px">(001) 234-56789</p>

  <div class="abs foot-title" style="left:611px">Information</div>
  <nav class="abs foot-links" style="left:611px;top:105px">
    <a>Shop</a><a>Blog</a><a>About</a><a>Contact Us</a>
  </nav>

  <div class="abs foot-title" style="left:770px">Join Our Newsletter</div>
  <div class="abs newsletter-input">Email</div>
  <div class="abs newsletter-btn">SUBMIT</div>
  <span class="abs social-ring" style="left:767px"></span>
  <span class="abs social-ring" style="left:814px"></span>
  <span class="abs social-ring" style="left:861px"></span>
  <span class="abs social-ring" style="left:908px"></span>

  <div class="abs foot-rule"></div>
  <div class="abs copyright">Copyrights © 2021 PaceKite. All rights reserved.</div>
</footer>

</body>
</html>
```